FinTech company looking to revamp and expand client-facing interface for our financial models

Pellworth Engines currently has a very simple website that allows clients to interact with our financial models. We are looking to completely redesign the current site and add several extra pages to provide extra functionality. We want the design to have a modern, slick feel, that will work on both a desktop or a tablet. It should be straightforward for clients to move between different pages at any time, and clear from the layout how to interact with the more advanced features. We have included screenshots of existing pages in the attached design brief, as well as sketches of the functionality required by the new pages, but can't provide a direct link to the current site.
Target Market(s)
Professional investors that will be paying to access the interface
Industry/Entity Type
Finance
Number of Pages Required
4 page
Colors
Designer to choose colors to be used in the design.
Look and feel
Each slider illustrates characteristics of the customer's brand and the style your logo design should communicate.

```html
<!DOCTYPE html>
<html lang="en">
<head>
<meta charset="utf-8">
<title>QFORGE – Models</title>
<link href="https://fonts.googleapis.com/css2?family=Montserrat:wght@500;600;700&family=Roboto+Condensed:wght@400;500&family=Open+Sans:wght@400;600;700&display=swap" rel="stylesheet">
<style>
:root{
  --navy:#0d3466;
  --teal:#0b6b63;
  --ink:#111;
  --frame:#e4e4e4;
  --stage:#ededed;
  --panel:#f4f4f4;
  --line:#dcdcdc;
  --row-alt:#efefef;
  --tab:#ffffff;
  --tab-dark:#141414;
  --filter-gray:#c9c9c9;
  --filter-head:#676767;
}
*{box-sizing:border-box;margin:0;padding:0}
html,body{width:1200px;height:706px;overflow:hidden;background:var(--frame)}
.canvas{position:absolute;left:0;top:0;width:1300px;height:765px;transform:scale(.92308);transform-origin:0 0;background:var(--frame);font-family:"Montserrat",sans-serif;color:var(--ink)}
.abs{position:absolute}
.stage{left:15px;top:0;width:1270px;height:750px;background:linear-gradient(#e9e9e9,#f3f3f3)}
.topbar{left:15px;top:0;width:1270px;height:75px;background:#fff;display:flex;box-shadow:0 3px 8px rgba(0,0,0,.08)}
.topbar .item{height:75px;display:flex;align-items:center;justify-content:center;gap:10px;font-weight:700;font-size:13px;border-right:1px solid #eee}
.topbar .brand{width:180px;font-size:17px}
.topbar .active{background:var(--navy);color:#fff}
.topbar svg{width:24px;height:24px}
.tabs .tab{position:absolute;display:flex;align-items:center;justify-content:center;font-weight:600;font-size:13px;color:#555;background:var(--tab);border-radius:6px 6px 0 0}
.tabs .tab.current{background:var(--tab-dark);color:#fff;font-size:12px}
.tabs .tab.small{font-size:12.5px}
.workspace{left:15px;top:170px;width:1270px;height:580px;background:var(--panel)}
.export{left:1165px;top:212px;display:flex;align-items:center;gap:8px;font-weight:700;font-size:17px;color:var(--navy)}
.models{left:105px;top:250px;width:1160px;border-collapse:collapse;font-family:"Roboto Condensed",sans-serif;font-size:16px;background:#fff;box-shadow:0 2px 8px rgba(0,0,0,.08);border-radius:6px;overflow:hidden}
.models th{background:var(--teal);color:#fff;font-family:"Montserrat",sans-serif;font-weight:600;font-size:16px;height:70px;text-align:left;padding-left:10px;border-right:1px solid rgba(255,255,255,.15)}
.models td{height:69px;padding-left:9px;border-right:1px solid #e2e2e2;line-height:1.3}
.models tr:nth-child(even) td{background:var(--row-alt)}
.filters{left:15px;top:115px;width:400px;height:310px;background:var(--filter-gray)}
.filters-tab{left:400px;top:145px;width:65px;height:250px;background:var(--filter-gray)}
.filters-tab span{position:absolute;left:22px;top:160px;transform:rotate(-90deg);transform-origin:0 0;font-weight:600;font-size:15px;letter-spacing:1px}
.collapse{left:453px;top:258px;width:26px;height:26px;border-radius:50%;background:var(--navy);border:2px solid #fff;display:flex;align-items:center;justify-content:center}
.filter-card{left:30px;top:130px;width:370px;height:280px;background:#fff;font-family:"Open Sans",sans-serif;font-size:16px}
.filter-card header{height:50px;background:var(--filter-head);color:#fff;font-weight:700;font-size:18px;display:flex;align-items:center;justify-content:center}
.frow{height:50px;display:flex;align-items:center;padding-left:16px;border-bottom:1px solid #e6e6e6}
.frow .lbl{width:85px}
.frow b{font-weight:700;margin-right:12px}
.frow input{width:150px;height:30px;border:1px solid #ccc;border-radius:5px;font:16px "Open Sans",sans-serif;padding-left:12px}
.check{display:inline-flex;align-items:center;gap:8px;font-weight:600;margin-left:22px}
.check i{width:20px;height:20px;border:1px solid #aaa;border-radius:3px;background:#fafafa}
.search{left:108px;top:215px;width:155px;height:50px;background:var(--navy);color:#fff;font-family:"Montserrat",sans-serif;font-weight:600;font-size:15px;display:flex;align-items:center;justify-content:center;border-radius:2px}
</style>
</head>
<body>
<div class="canvas">
  <div class="abs stage"></div>

  <nav class="abs topbar">
    <div class="item brand">QFORGE</div>
    <div class="item active" style="width:90px">250D</div>
    <div class="item" style="width:90px">83D</div>
    <div class="item" style="width:90px">42D</div>
    <div class="item" style="width:135px"></div>
    <div class="item active" style="width:141px">
      <svg viewBox="0 0 24 24" fill="none" stroke="#fff" stroke-width="2"><path d="M3 11 12 3l9 8M5 10v10h5v-6h4v6h5V10"/></svg>MODELS</div>
    <div class="item" style="width:177px">
      <svg viewBox="0 0 24 24" fill="none" stroke="#222" stroke-width="1.6"><circle cx="12" cy="12" r="4"/><circle cx="12" cy="12" r="8.5" stroke-dasharray="2 2"/></svg>SENSITIVITIES</div>
    <div class="item" style="width:160px">
      <svg viewBox="0 0 24 24" fill="none" stroke="#222" stroke-width="1.8"><circle cx="7" cy="7" r="4"/><circle cx="17" cy="7" r="4"/><circle cx="7" cy="17" r="4"/><circle cx="17" cy="17" r="4"/></svg>PORTFOLIO</div>
    <div class="item" style="width:152px">
      <svg viewBox="0 0 24 24" fill="none" stroke="#222" stroke-width="1.8"><rect x="3" y="4" width="18" height="16"/><path d="M6 16l4-5 3 3 5-6"/></svg>BACKTEST</div>
  </nav>

  <div class="abs workspace"></div>

  <div class="tabs">
    <div class="tab" style="left:400px;top:125px;width:145px;height:45px">PAIRS</div>
    <div class="tab current" style="left:550px;top:115px;width:155px;height:55px">ETF PAIRS</div>
    <div class="tab" style="left:712px;top:125px;width:153px;height:45px">FACTORS</div>
    <div class="tab small" style="left:870px;top:135px;width:155px;height:35px">NEW TAB TITLE #1</div>
    <div class="tab small" style="left:1030px;top:135px;width:155px;height:35px">NEW TAB TITLE #2</div>
    <div class="tab" style="left:1190px;top:135px;width:40px;height:35px">
      <svg width="14" height="20" viewBox="0 0 14 20"><path d="M3 2l8 8-8 8" fill="none" stroke="#999" stroke-width="3"/></svg></div>
    <div class="tab" style="left:1235px;top:135px;width:40px;height:35px;background:var(--navy);border-radius:4px">
      <svg width="26" height="26" viewBox="0 0 26 26" fill="none" stroke="#fff" stroke-width="2"><circle cx="13" cy="13" r="11"/><path d="M13 7v12M7 13h12"/></svg></div>
  </div>

  <div class="abs export">
    <svg width="26" height="24" viewBox="0 0 26 24" fill="none" stroke="#0d3466" stroke-width="2.4"><path d="M12 5H3v17h17v-7"/><path d="M9 16c1-7 6-10 14-10M18 2l5 4-5 4"/></svg>Export
  </div>

  <table class="abs models">
    <thead><tr>
      <th style="width:100px"></th><th style="width:140px"></th><th style="width:115px"></th>
      <th style="width:85px">Quality</th><th style="width:90px">Stat 1</th><th style="width:90px">Stat 2</th><th style="width:90px">Stat 3</th><th style="width:90px">Stat 4</th><th style="width:90px">Stat 5</th><th style="width:90px">Stat 6</th><th style="width:90px">Stat 7</th><th style="width:90px">Stat 8</th>
    </tr></thead>
    <tbody>
      <tr><td>Model 1</td><td>Energy</td><td>2019-07-03<br>12:15:00.000</td><td>30.2288</td><td>2.01574</td><td>23.305</td><td>-0.149368</td><td>22.3054</td><td>4.63714</td><td>0.945706</td><td>2.81949</td><td>2.60858</td></tr>
      <tr><td>Model 2</td><td>Industrials</td><td>2019-07-03<br>12:15:00.000</td><td>32.8694</td><td>0.87307</td><td>32.185</td><td>-0.033692</td><td>33.9911</td><td>11.5693</td><td>-0.472968</td><td>-0.830458</td><td>6.80646</td></tr>
      <tr><td>Model 3</td><td>Consumer<br>Discretionary</td><td>2019-07-03<br>12:15:00.000</td><td>1.66002</td><td>-0.569222</td><td>159.814</td><td>0.0252328</td><td>172.616</td><td>10.2875</td><td>-0.750396</td><td>-0.385309</td><td>4.69146</td></tr>
      <tr><td>Model 4</td><td>Information<br>Technology</td><td>2019-07-03<br>12:15:00.000</td><td>45.6856</td><td>0.412148</td><td>202.488</td><td>0.0084923</td><td>205.834</td><td>11.9094</td><td>-0.137913</td><td>0.449595</td><td>3.85106</td></tr>
      <tr><td>Model 5</td><td>Information<br>Technology</td><td>2019-07-03<br>12:15:00.000</td><td>75.7733</td><td>7.06728</td><td>188.605</td><td>0.016913</td><td>161.665</td><td>3.82241</td><td>0.981019</td><td>1.29847</td><td>3.34927</td></tr>
    </tbody>
  </table>

  <aside>
    <div class="abs filters"></div>
    <div class="abs filters-tab"><span>FILTERS</span></div>
    <div class="abs collapse"><svg width="14" height="14" viewBox="0 0 14 14" fill="none" stroke="#fff" stroke-width="2"><path d="M12 7H2M6 3 2 7l4 4"/></svg></div>
    <div class="abs filter-card">
      <header>Filters</header>
      <div class="frow"><span class="lbl">Quality</span><b>Threshold:</b><input value="-10"></div>
      <div class="frow"><span class="lbl"><b style="margin:0">Abs.</b> Stat</span><b>Threshold:</b><input value="-10"></div>
      <div class="frow"><b style="margin:0">Apply</b><span class="check"><i></i>All tabs</span><span class="check"><i></i>Current tab</span></div>
      <div class="abs search">SEARCH</div>
    </div>
  </aside>
</div>
</body>
</html>
```